Brenwick Structures Construction Company Seeking Modern Website

We are a small construction company wanting to create a web presence. We don't have much in the way of current content but will get photos as they come in. Attached is a picture of our business card.
The pages we would like on the menu are:
Home
Portfolio
Product Specs
Testimonials
Our Process
Contact
Some designs we like are:
http://www.tovasheds-example.com/
http://www.qrnstructures-example.com/
http://dunholtbarns-example.com/
http://pellingframes-example.com/
Not much requirements other than that so feel free to be creative!
Updates
Target Market(s)
Construction
Commercial and Residential Buildings
Industry/Entity Type
Construction Company
Number of Pages Required
5+ page
Look and feel

```html
<!DOCTYPE html>
<html lang="en">
<head>
<meta charset="utf-8">
<title>Brenwick Structures – Building Dreams</title>
<link href="https://fonts.googleapis.com/css2?family=Open+Sans:wght@300;400;600;700&family=Dancing+Script:wght@600&display=swap" rel="stylesheet">
<style>
:root{
  --red:#e3362a;
  --red-dark:#b8241b;
  --cyan:#1ba6d8;
  --blue:#1596d3;
  --navy:#2b4f8f;
  --ink:#333;
  --muted:#666;
  --light:#f2f2f2;
  --footer:#2c2b2a;
  --footer-deep:#1d1c1b;
  --line:#ddd;
}
*{margin:0;padding:0;box-sizing:border-box}
html,body{width:1200px;height:3315px;overflow:hidden}
body{position:relative;font-family:"Open Sans",Arial,sans-serif;color:var(--ink);background:#fff}
.abs{position:absolute}

/* header */
.hero{left:0;top:0;width:1200px;height:640px;background:linear-gradient(180deg,#9fc3e6 0%,#c9dbeb 30%,#6d655f 55%,#8a8079 70%,#4f7a35 88%,#3c6127 100%)}
.topbar{left:0;top:0;width:1200px;height:96px;background:#fff}
.brand{left:168px;top:24px;height:44px;display:flex;align-items:center;gap:10px;font-weight:700;font-size:26px;color:var(--navy)}
.brand-mark{width:22px;height:22px;background:var(--red)}
.contact-chip{top:30px;display:flex;align-items:center;gap:12px;font-size:16px;color:var(--ink)}
.contact-chip .ico{width:38px;height:30px;border-radius:15px;background:var(--red);display:flex;align-items:center;justify-content:center}
.contact-chip.mail{color:var(--cyan)}
.nav{left:0;top:88px;width:1200px;height:52px}
.nav ul{list-style:none;position:absolute;left:0;top:0;width:1200px;height:52px}
.nav li{position:absolute;top:8px;color:#fff;font-size:14px;line-height:17px;text-transform:uppercase}
.nav li small{display:block;text-transform:none;font-size:10px;opacity:.85;line-height:12px}
.tagline{left:0;top:292px;width:1200px;text-align:center;font-family:"Dancing Script",cursive;font-size:54px;color:#5fd2e8}

/* sections */
.section-title{width:1200px;left:0;text-align:center;font-weight:300;font-size:27px;color:var(--red);text-transform:uppercase;letter-spacing:.5px}
.section-lead{left:80px;width:1040px;text-align:center;font-size:13.5px;line-height:22px;color:var(--muted)}
.services{left:0;top:640px;width:1200px;height:565px;background:var(--light)}
.service{width:242px}
.service .photo{width:242px;height:188px;border:2px solid #bcd;}
.service h3{margin-top:46px;font-size:14px;font-weight:400;color:var(--cyan);text-transform:uppercase}
.service p{margin-top:22px;font-size:13px;line-height:19px;color:var(--muted)}

.process-step{width:320px;text-align:center}
.process-step .icon{width:88px;height:88px;border-radius:50%;margin:0 auto;display:flex;align-items:center;justify-content:center}
.process-step h3{margin-top:36px;font-size:19px;font-weight:400;color:var(--cyan);text-transform:uppercase}
.process-step p{margin-top:14px;font-size:12.5px;line-height:21px;color:var(--muted)}
.rule{left:0;top:1586px;width:1200px;height:2px;background:#f0a8a3}

.portfolio{left:0;top:1588px;width:1200px;height:522px;background:linear-gradient(180deg,#fafafa,#eee 60%,#f7f7f7)}
.shot{top:1772px;height:265px}

.products{left:0;top:2110px;width:1200px;height:498px;background:var(--blue)}
.products .section-title,.products .section-lead{color:#fff}
.product{top:2302px;width:320px;height:240px;background:#fff}
.product-feature{background:var(--navy);border:4px solid #5f82c4;color:#fff;text-align:center}
.product-feature h4{margin-top:50px;font-weight:400;font-size:17px;text-transform:uppercase}
.product-feature p{font-size:12px;line-height:17px;margin-top:8px}
.btn{display:inline-block;margin-top:14px;background:#fff;color:var(--navy);font-size:13px;font-weight:600;padding:6px 12px}
.arrow{top:2392px;width:60px;height:60px;border-radius:50%;background:#1a5faa;border:3px solid #fff;display:flex;align-items:center;justify-content:center}

.quote{top:2714px;width:490px;height:137px;border:2px solid #222;border-radius:6px;padding:20px 90px 0 24px;font-size:12.5px;line-height:19px;color:#444}
.quote b{display:block;margin-top:10px;font-weight:600;font-size:12px;line-height:14px}
.quote span{font-size:11px}
.avatar{width:100px;height:100px;border-radius:50%;border:4px solid var(--blue);background:radial-gradient(circle at 50% 40%,#b9c6d3,#5d7184)}

/* footer */
.footer{left:0;top:2966px;width:1200px;height:301px;background:var(--footer);color:#ddd}
.footer h5{font-size:14px;font-weight:600;color:var(--cyan);padding-bottom:8px;border-bottom:1px solid #555}
.footer-col{top:30px}
.foot-nav{list-style:none;font-size:12px}
.foot-nav li{padding:8px 10px;border-bottom:1px solid #444;line-height:15px}
.footer .small{font-size:12px;line-height:17px}
.copyright{left:0;top:3267px;width:1200px;height:48px;background:var(--footer-deep);color:#bbb;font-size:11px;text-align:center;line-height:48px}
.subscribe{display:flex;margin-top:12px}
.subscribe span{width:170px;height:24px;background:#fff;color:#777;font-size:11px;line-height:24px;padding-left:8px}
.subscribe b{background:var(--cyan);color:#fff;font-size:11px;font-weight:400;line-height:24px;padding:0 8px}
.social{display:flex;gap:8px;margin-top:14px;margin-left:92px}
.social i{width:28px;height:28px;background:#3a7bc8;display:block}
</style>
</head>
<body>

<div class="abs hero" role="img" aria-label="Photo of a large stone family house with twin garage doors under a blue sky"></div>

<header>
  <div class="abs topbar"></div>
  <div class="abs brand"><span class="brand-mark"></span>Brenwick Structures</div>
  <div class="abs contact-chip" style="left:634px">
    <span class="ico"><svg width="16" height="16" viewBox="0 0 24 24"><path fill="#fff" d="M6.6 10.8a15 15 0 0 0 6.6 6.6l2.2-2.2c.3-.3.7-.4 1-.2 1.1.4 2.3.6 3.6.6.6 0 1 .4 1 1V20c0 .6-.4 1-1 1A17 17 0 0 1 3 4c0-.6.4-1 1-1h3.5c.6 0 1 .4 1 1 0 1.3.2 2.5.6 3.6.1.3 0 .7-.2 1z"/></svg></span>800 555 0182
  </div>
  <div class="abs contact-chip mail" style="left:796px">
    <span class="ico"><svg width="16" height="12" viewBox="0 0 16 12"><rect x="0.5" y="0.5" width="15" height="11" fill="#fff"/><path d="M1 1l7 6 7-6" stroke="#e3362a" fill="none"/></svg></span>info@brenwickstructures-example.com
  </div>
  <nav class="abs nav">
    <svg class="abs" width="1200" height="52" viewBox="0 0 1200 52" style="left:0;top:0">
      <path d="M0 0H1200V6H1120L1080 44H120L80 6H0Z" fill="#fff"/>
      <path d="M70 0L120 52H1080L1130 0Z" fill="var(--red)"/>
      <path d="M120 52H1080" stroke="var(--red-dark)" stroke-width="3"/>
    </svg>
    <ul>
      <li style="left:168px">Home<small>The Beginning</small></li>
      <li style="left:292px">Portfolio<small>That Inspire</small></li>
      <li style="left:451px">Products<small>That Deliver</small></li>
      <li style="left:606px">Testimonials<small>What Others Say</small></li>
      <li style="left:785px">Our Process<small>Good Process</small></li>
      <li style="left:961px">Contact<small>Get In Touch</small></li>
    </ul>
  </nav>
</header>

<h1 class="abs tagline">Building Dreams So You Can Build Dreams</h1>

<section class="abs services">
  <h2 class="abs section-title" style="top:48px">Our Services</h2>
  <p class="abs section-lead" style="top:100px">Lorem ipsum dolor sit amet, consectetur adipiscing elit. Praesent rutrum sem quam, vel dignissim lacus placerat quis. Nunc et turpis nec massa vulputate efficitur ut Proin accumsan at massa eget dapibus. Ut sollicitudin id est non auctor. Praesent ut tincidunt elit.</p>
  <div class="abs service" style="left:80px;top:189px">
    <div class="photo" role="img" aria-label="Photo of two builders in hard hats reviewing plans" style="background:linear-gradient(135deg,#34506e,#8da2b6 60%,#d4b44a)"></div>
    <h3>General Contracting</h3>
    <p>Construction Department Specializing in Commercial Remodeling and Maintenance.</p>
  </div>
  <div class="abs service" style="left:346px;top:189px">
    <div class="photo" role="img" aria-label="Photo of carpenters framing a timber structure" style="background:linear-gradient(135deg,#c9926a,#9a5a35 55%,#e0b58e)"></div>
    <h3>Construction</h3>
    <p>Brenwick Structures has spent a century refining our construction and safety practices.</p>
  </div>
  <div class="abs service" style="left:612px;top:189px">
    <div class="photo" role="img" aria-label="Photo of a worker laying floor tiles" style="background:linear-gradient(135deg,#777,#b68d55 55%,#d9b67a)"></div>
    <h3>Commercial Maintenance</h3>
    <p>Brenwick Structures has skilled technicians ready to repair and maintain commercial facilities.</p>
  </div>
  <div class="abs service" style="left:878px;top:189px">
    <div class="photo" role="img" aria-label="Photo of a painter rolling paint onto a wall" style="background:linear-gradient(135deg,#cfe8e4,#9fd3cc 55%,#e6eef0)"></div>
    <h3>Painting</h3>
    <p>Our Painting Division is staffed with professional painters who have lots of experience in the field of projects.</p>
  </div>
</section>

<section>
  <h2 class="abs section-title" style="top:1252px">Our Process</h2>
  <div class="abs process-step" style="left:85px;top:1319px">
    <div class="icon" style="background:#3db54a"><svg width="40" height="40" viewBox="0 0 40 40" fill="#fff"><circle cx="13" cy="12" r="5"/><circle cx="27" cy="12" r="5"/><rect x="6" y="19" width="28" height="4"/><rect x="9" y="23" width="4" height="10"/><rect x="27" y="23" width="4" height="10"/></svg></div>
    <h3>Requirement</h3>
    <p>Our home owners show us what work<br>they require to be done.</p>
  </div>
  <div class="abs process-step" style="left:439px;top:1319px">
    <div class="icon" style="background:#23b6d6"><svg width="40" height="40" viewBox="0 0 40 40" fill="#fff"><rect x="8" y="8" width="26" height="18"/><rect x="11" y="27" width="3" height="7"/><circle cx="9" cy="22" r="4"/></svg></div>
    <h3>Choice</h3>
    <p>We then offer our clients a choice of<br>guaranteed “Brenwick Structures”.</p>
  </div>
  <div class="abs process-step" style="left:795px;top:1319px">
    <div class="icon" style="background:#7d45b8"><svg width="40" height="40" viewBox="0 0 40 40" fill="#fff"><rect x="6" y="10" width="8" height="14"/><rect x="26" y="10" width="8" height="14"/><rect x="12" y="17" width="16" height="5"/><rect x="6" y="26" width="28" height="4"/></svg></div>
    <h3>Full Responsibility</h3>
    <p>Once approved by our customers, the people at Brenwick Structures Services then take FULL responsibility to complete the works.</p>
  </div>
</section>
<div class="abs rule"></div>

<section class="abs portfolio">
  <h2 class="abs section-title" style="top:48px">Our Portfolio</h2>
  <p class="abs section-lead" style="top:100px">Lorem ipsum dolor sit amet, consectetur adipiscing elit. Praesent rutrum sem quam, vel dignissim lacus placerat quis. Nunc et turpis nec massa vulputate efficitur ut Proin accumsan at massa eget dapibus. Ut sollicitudin id est non auctor. Praesent ut tincidunt elit.</p>
</section>
<div class="abs shot" style="left:0;width:354px;background:linear-gradient(180deg,#9cc3e8,#d9d9d9 50%,#6e7a63 85%,#4e8a35)" role="img" aria-label="Photo of a modern white two-storey home"></div>
<div class="abs shot" style="left:354px;width:356px;background:linear-gradient(180deg,#8a3a45,#a27a8e 50%,#6b5d80)" role="img" aria-label="Photo of a suburban house framed by autumn trees at dusk"></div>
<div class="abs shot" style="left:710px;width:358px;background:linear-gradient(180deg,#5f92d0,#b59c78 45%,#6aa242 80%,#4b8a2a)" role="img" aria-label="Photo of a stone and siding house with a landscaped garden"></div>
<div class="abs shot" style="left:1068px;width:132px;background:linear-gradient(180deg,#a5c5e0,#e8e6df 50%,#8fa77c)" role="img" aria-label="Photo of a white porch-front house"></div>

<section class="abs products">
  <h2 class="abs section-title" style="top:50px">Products</h2>
  <p class="abs section-lead" style="top:98px">Lorem ipsum dolor sit amet, consectetur adipiscing elit. Praesent rutrum sem quam, vel dignissim lacus placerat quis. Nunc et turpis nec massa vulputate efficitur ut Proin accumsan at massa eget dapibus. Ut sollicitudin id est non auctor. Praesent ut tincidunt elit.</p>
</section>
<div class="abs product product-feature" style="left:122px">
  <h4>Red Door</h4>
  <p>lorem Ipsum<br>Ipsum Door<br>Integrated Red Door</p>
  <span class="btn">VIEW PRODUCT</span>
</div>
<div class="abs product" style="left:442px;width:320px"><div class="abs" style="left:90px;top:20px;width:140px;height:200px;background:linear-gradient(180deg,#f1f1f1,#e4d9cc 40%,#c4322c 75%,#eee)" role="img" aria-label="Photo of a paint brush dipped in red paint"></div></div>
<div class="abs product" style="left:762px;width:320px"><div class="abs" style="left:10px;top:10px;width:300px;height:220px;background:radial-gradient(circle at 50% 50%,#fff 20%,#f2cfc8 45%,#6b2d28 80%)" role="img" aria-label="Photo of an open red-framed window"></div></div>
<div class="abs arrow" style="left:96px"><svg width="20" height="20" viewBox="0 0 20 20"><path d="M13 3L6 10l7 7" stroke="#fff" stroke-width="3" fill="none"/></svg></div>
<div class="abs arrow" style="left:1042px"><svg width="20" height="20" viewBox="0 0 20 20"><path d="M7 3l7 7-7 7" stroke="#fff" stroke-width="3" fill="none"/></svg></div>

<section>
  <h2 class="abs section-title" style="top:2650px">Testimonials</h2>
  <blockquote class="abs quote" style="left:88px">Lorem ipsum dolor sit amet, consectetur adipiscing elit. Nulla fermentum dignissim risus eleifend sagittis. Integer turpis mi, hendrerit a leo eu, vestibulum dictum sem. Nullam egestas mauris in dui cursus, nec porta lectus tempus.<b>Martin Reyes</b><span>Customer</span></blockquote>
  <div class="abs avatar" style="left:464px;top:2795px" role="img" aria-label="Customer portrait"></div>
  <blockquote class="abs quote" style="left:617px">Lorem ipsum dolor sit amet, consectetur adipiscing elit. Nulla fermentum dignissim risus eleifend sagittis. Integer turpis mi, hendrerit a leo eu, vestibulum dictum sem. Nullam egestas mauris in dui cursus, nec porta lectus tempus.<b>Martin Reyes</b><span>Customer</span></blockquote>
  <div class="abs avatar" style="left:993px;top:2795px" role="img" aria-label="Customer portrait"></div>
</section>

<footer class="abs footer">
  <div class="abs footer-col" style="left:80px;width:154px">
    <h5>Navigation</h5>
    <ul class="foot-nav">
      <li>Home</li><li>About</li><li>Services</li><li>Portfolio</li><li>Harlow Family</li><li>Testimonial</li><li>Contact</li>
    </ul>
  </div>
  <div class="abs footer-col" style="left:272px;width:262px">
    <h5>News &amp; Updates</h5>
    <div class="abs" style="left:0;top:48px;width:124px;height:114px;border:3px solid #666;background:linear-gradient(180deg,#9ab4cf,#4a4a4a 70%)" role="img" aria-label="Photo of a newly built house"></div>
    <p class="abs small" style="left:134px;top:44px;width:128px">Lorem ipsum dolor sit amet, consectetur adipiscing elit. Fusce convallis libero quis fellstor malesuada. Nam ultrices et velit sed maximus.</p>
    <p class="abs small" style="left:0;top:176px;width:262px">Mauris ante nisl, facilisis vel condimentum id, tristique at mauris. Donec ex nisi, lacinia non efficitur id, scelerisque id dolor. Vivamus euismod velit eget velit iaculis placerat.</p>
  </div>
  <div class="abs footer-col" style="left:577px;width:240px">
    <h5>Our Location</h5>
    <p class="small" style="margin-top:12px;display:flex;gap:8px"><svg width="10" height="14" viewBox="0 0 10 14"><path d="M5 0a5 5 0 0 1 5 5c0 4-5 9-5 9S0 9 0 5a5 5 0 0 1 5-5z" fill="#ddd"/></svg><span>Address Address Address Address<br>Address Address Address</span></p>
    <p style="margin-top:8px;font-size:16px;display:flex;gap:8px;align-items:center"><svg width="12" height="14" viewBox="0 0 24 24"><path fill="#fff" d="M6.6 10.8a15 15 0 0 0 6.6 6.6l2.2-2.2c.3-.3.7-.4 1-.2 1.1.4 2.3.6 3.6.6.6 0 1 .4 1 1V20c0 .6-.4 1-1 1A17 17 0 0 1 3 4c0-.6.4-1 1-1h3.5c.6 0 1 .4 1 1 0 1.3.2 2.5.6 3.6.1.3 0 .7-.2 1z"/></svg>800 555 0182</p>
    <p class="small" style="margin-top:8px;font-size:11px">✉ info@brenwickstructures-example.com</p>
    <div style="margin-top:14px;width:240px;height:110px;border:3px solid #888;background:linear-gradient(135deg,#e8e4d8,#d3dcc4 50%,#e8e0cc)" role="img" aria-label="Street map showing the office location"></div>
  </div>
  <div class="abs footer-col" style="left:862px;width:258px">
    <h5>Newsletter Signup</h5>
    <p class="small" style="margin-top:10px;font-size:11px;line-height:15px">Please enter your email address below to<br>receive our FREE newsletter</p>
    <div class="subscribe"><span>Your Email ID</span><b>Subscribe</b></div>
    <div class="social" aria-label="Social links"><i></i><i style="background:#e8742a"></i><i style="background:#3b5b9a"></i><i style="background:#c8302a"></i></div>
  </div>
</footer>
<div class="abs copyright">Copyright 2015 @brenwickstructures-example.com. All rights reserved</div>

</body>
</html>
```